Alaska Law Firm Needs a Sticker Design

We need a design for stickers to put on already-printed brochures. We mail the brochures to potential clients so they can learn more about accident-induced injuries, insurance claims, legal representation, and our own law firm.

One of our lawyers wrote a book that provides a helpful overview of personal injury claims. We are offering this book for free to anyone who calls and requests it. Therefore, the sticker design should include one of the following phrases, or something very similar:
a) "Still have questions? Call and request our book-- for free!"
b) "Still have questions about auto accident claims? Call and request our book today."
c) "Still have questions about filing a claim? Call and request a free copy of our book."
d) "Still have questions? Call us today to request a free copy of our book, Clear Lanes Ahead."
e) "To learn more about automobile accidents and insurance, call today and request a free copy of our book."

The sticker should be approximately 3"x3" and may be a circle, square, rectangle, or ellipsis. The sticker will be placed on the back of the folder, which is light blue. We would like the sticker to match the color scheme of our website and the folder.

I will upload an image of the book cover as soon as I obtain it.

Law Firm

Font styles to use
Serif
Sans Serif

Requirements
Should not have
• Bright colors that aren't already used in the folder design. e.g. no bright orange, pink, chartreuse, turquoise, yellow, red.

```html
<!DOCTYPE html>
<html lang="en">
<head>
<meta charset="utf-8">
<title>Free Book Sticker</title>
<link href="https://fonts.googleapis.com/css2?family=Cinzel:wght@400;500&family=Arimo:wght@400&family=Oswald:wght@300;700&family=Open+Sans:wght@400;600&display=swap" rel="stylesheet">
<style>
  :root{
    --paper:#ffffff;
    --sky:#d9e6f6;
    --navy:#143d66;
    --navy-ink:#16406b;
    --pale-text:#e4eefa;
    --book-navy:#171b47;
    --book-red:#c8242b;
    --book-text:#33384d;
  }
  *{margin:0;padding:0;box-sizing:border-box}
  html,body{width:1200px;height:1200px;overflow:hidden;background:var(--paper)}
  .canvas{position:relative;width:1200px;height:1200px;background:var(--paper)}

  .sticker{position:absolute;left:0;top:65px;width:1200px;height:1118px;border-radius:50%;
    background:var(--sky);overflow:hidden;border:1.5px solid var(--navy)}
  .band{position:absolute;left:0;width:100%;background:var(--navy)}
  .band--offer{top:323px;height:216px}
  .band--phone{top:981px;height:200px}

  .line{position:absolute;left:0;width:1200px;text-align:center;line-height:1;white-space:nowrap}
  .headline-small{top:150px;font-family:'Cinzel',serif;font-size:100px;color:var(--navy-ink);letter-spacing:2px}
  .headline-big{top:258px;font-family:'Cinzel',serif;font-size:128px;color:var(--navy-ink);letter-spacing:1px}
  .offer-top{top:428px;font-family:'Cinzel',serif;font-size:62px;color:var(--pale-text);letter-spacing:2px}
  .offer-bottom{top:505px;font-family:'Cinzel',serif;font-size:90px;color:var(--pale-text);letter-spacing:4px}
  .phone{top:1072px;font-family:'Arimo',sans-serif;font-size:54px;color:var(--pale-text)}

  .book{position:absolute;left:358px;top:641px;width:467px;height:359px;border:2px solid #111;background:var(--paper);overflow:hidden}
  .back{position:absolute;left:0;top:0;width:230px;height:100%;background:var(--paper);font-family:'Open Sans',sans-serif;color:var(--book-text)}
  .back p{position:absolute;font-size:5.4px;line-height:1.3;text-align:justify}
  .back .teaser{left:18px;top:16px;width:196px;color:var(--book-red);font-weight:600;text-align:center;text-transform:uppercase}
  .back .intro-1{left:22px;top:42px;width:196px}
  .back .intro-2{left:22px;top:66px;width:196px}
  .back .rule{position:absolute;left:38px;top:101px;width:160px;height:1px;background:var(--book-red)}
  .back .portrait{position:absolute;left:21px;top:113px;width:57px;height:75px;background:linear-gradient(180deg,#c9d2de,#3b5fa6 70%,#223a78)}
  .back .bio-1{left:84px;top:113px;width:138px}
  .back .bio-2{left:84px;top:142px;width:138px}
  .back .bio-3{left:22px;top:196px;width:200px}
  .back .bio-4{left:22px;top:222px;width:200px}
  .back .firm{position:absolute;left:22px;top:288px;display:flex;align-items:center;gap:4px;
    font-family:'Open Sans',sans-serif;font-size:10px;color:var(--book-navy);line-height:1;text-transform:uppercase}
  .back .firm .mark{width:12px;height:12px;background:var(--book-navy)}
  .back .strip{position:absolute;left:0;bottom:0;width:100%;height:40px;background:var(--book-navy)}
  .back .strip .blank{position:absolute;left:140px;top:0;width:80px;height:24px;background:var(--paper)}

  .spine{position:absolute;left:230px;top:0;width:8px;height:100%;background:var(--book-navy)}
  .spine span{position:absolute;left:1px;top:114px;writing-mode:vertical-rl;font-family:'Open Sans',sans-serif;
    font-size:5px;color:#fff;white-space:nowrap;letter-spacing:.3px}

  .front{position:absolute;left:238px;top:0;width:229px;height:100%;background:var(--paper);text-align:center}
  .front .author{position:absolute;left:0;top:16px;width:100%;font-family:'Oswald',sans-serif;font-weight:300;font-size:15px;color:var(--book-navy);line-height:1}
  .front .title{position:absolute;left:0;top:38px;width:100%;font-family:'Oswald',sans-serif;font-weight:700;font-size:27px;line-height:.98;color:var(--book-navy);letter-spacing:-.5px}
  .front .photo{position:absolute;left:2px;top:105px;width:227px;height:212px;background:linear-gradient(180deg,#e7eef1 0%,#b9cf9a 45%,#6f9a3d 75%,#5a8a2d 100%)}
  .front .subtitle{position:absolute;left:0;bottom:0;width:100%;height:40px;background:var(--book-navy);color:#fff;
    font-family:'Open Sans',sans-serif;font-size:10.5px;line-height:1.3;padding-top:5px;text-transform:uppercase}
</style>
</head>
<body>
<div class="canvas">
  <div class="sticker">
    <div class="band band--offer"></div>
    <div class="band band--phone"></div>
  </div>

  <div class="line headline-small">Still have</div>
  <div class="line headline-big">QUESTIONS?</div>
  <div class="line offer-top">CALL AND REQUEST OUR BOOK</div>
  <div class="line offer-bottom">FOR FREE</div>

  <div class="book">
    <div class="back">
      <p class="teaser">Most drivers will face at least one accident in their lifetime. Know what to do when it happens.</p>
      <p class="intro-1">If you have avoided an accident so far, consider yourself lucky. It is always best to be prepared for when it happens.</p>
      <p class="intro-2">If you were recently in a crash and are unsure what comes next, this book explains your rights and the proper steps to take.</p>
      <div class="rule"></div>
      <div class="portrait" role="img" aria-label="Author portrait photograph"></div>
      <p class="bio-1">Daniel studied science before choosing law school over a medical career, then began his practice defending doctors and hospitals.</p>
      <p class="bio-2">He soon learned that his true calling was helping injured people stand up to insurance companies.</p>
      <p class="bio-3">Today his firm helps Alaskans get full and fair compensation for their injuries.</p>
      <p class="bio-4">While most cases settle out of court, insurers pay fairly when they know the firm is ready for trial.</p>
      <div class="firm"><span class="mark"></span>Whitmore Law Group</div>
      <div class="strip"><div class="blank"></div></div>
    </div>
    <div class="spine"><span>CLEAR LANES AHEAD &nbsp;&nbsp; DANIEL R. WHITMORE</span></div>
    <div class="front">
      <div class="author">DANIEL R. WHITMORE</div>
      <div class="title">CLEAR LANES<br>AHEAD</div>
      <div class="photo" role="img" aria-label="Cover photograph of a smiling family lying on the grass in a park beside a small red car"></div>
      <div class="subtitle">The right way to handle<br>your auto accident claim</div>
    </div>
  </div>

  <div class="line phone">(907) 555- 0142</div>
</div>
</body>
</html>
```